New profile page for existing party website

For the party website 'Partyvenz' we need a new design for the user profile page.

The page should show
* a profile picture
* basic information like name, age and city
* music styles he/she likes
* links to their Chatterbook profile and website
* a bio (HTML content)
* events they plan to go to
* past events
* pictures

Challenge is that some users may have little information (just their name) while others have a huge description, lots of foto's, events, etc.

Please visit http://www.partyvenz.example and http://www.partyvenz.example/users/bertil

Target Market(s)

Men and women between 18 and 35

Industry/Entity Type

Night Club

Number of Pages Required

2 page

Font styles to use
Other font styles liked:
• Roboto

Requirements
Must have
• Please design how the page looks with a fully filled out profile and with an empty profile.
• It should fit well with the existing website.
• Include designs for both for small screens (mobile) and large screens (tablet, desktop).
Nice to have
• UX design on how to collapse or paginate sections.
• Interactive effects would be a bonus.
Should not have
• The page should not have subnavigation like menus or tabs.

```html
<!DOCTYPE html>
<html lang="nl">
<head>
<meta charset="utf-8">
<title>Partyvenz – Profiel</title>
<link rel="stylesheet" href="https://fonts.googleapis.com/css2?family=Open+Sans:wght@400;600;700&family=Raleway:wght@400;500;600&display=swap">
<style>
:root{
  --bg:#ecebf0;
  --ink:#2b2b2b;
  --muted:#555;
  --black:#111;
  --dark:#222;
  --orange:#f0801e;
  --rule:#d8d8d8;
  --white:#fff;
}
*{box-sizing:border-box;margin:0;padding:0}
html,body{width:1200px;height:4813px;overflow:hidden;background:var(--bg)}
body{font-family:"Open Sans",sans-serif;color:var(--ink)}
.page{position:absolute;left:270px;top:0;width:660px;height:4813px;background:var(--white);overflow:hidden}

.topbar{height:128px;background:var(--black);display:flex;align-items:center;justify-content:space-between;padding:0 36px 0 40px}
.brand{display:flex;align-items:center;gap:14px;color:var(--white);font-family:"Open Sans",sans-serif;font-weight:600;font-size:40px}
.brand-dot{width:18px;height:18px;border-radius:50%;background:var(--white)}
.topbar-icons{display:flex;align-items:center;gap:40px}

.hero{position:relative;height:610px;overflow:hidden;text-align:center;color:var(--white)}
.hero-photo{position:absolute;inset:0;background:radial-gradient(ellipse at 50% 30%,#7a5a48 0%,#3b2c27 45%,#1a1515 100%)}
.hero-shade{position:absolute;inset:0;background:linear-gradient(180deg,rgba(0,0,0,.15),rgba(0,0,0,.55))}
.hero-inner{position:relative;padding-top:36px}
.avatar{width:208px;height:208px;margin:0 auto;border-radius:50%;border:6px solid #c9c2bd;background:radial-gradient(circle at 50% 40%,#d18a5e,#7c3f2a 70%,#3a1f18)}
.profile-name{font-family:"Raleway",sans-serif;font-weight:500;font-size:50px;letter-spacing:2px;margin-top:22px}
.profile-meta{font-weight:700;font-size:19px;text-transform:uppercase;line-height:48px;margin-top:12px}
.profile-meta .sep{margin:0 16px}
.socials{display:flex;justify-content:center;gap:10px;margin-top:12px}
.social{width:46px;height:46px;border-radius:50%;background:var(--white)}

.bio{height:2146px;padding:50px 40px 0 52px}
.bio-block{padding-bottom:34px;border-bottom:2px solid var(--rule);margin-bottom:40px}
.bio-block:last-child{border:none}
.bio h2{font-family:"Raleway",sans-serif;font-weight:500;font-size:37px;color:var(--ink);margin-bottom:22px}
.bio p{font-size:20.5px;line-height:35px;color:var(--muted);margin-bottom:12px}
.conditions{list-style:none}
.conditions li{position:relative;padding-left:30px;font-size:20.5px;line-height:35px;color:var(--muted);margin-bottom:14px}
.conditions li::before{content:"";position:absolute;left:2px;top:12px;width:10px;height:10px;border-right:2px solid #777;border-top:2px solid #777;transform:rotate(45deg)}

.plans{height:680px;background:var(--dark);padding:44px 48px 0 88px;color:var(--white)}
.plans-head{display:flex;align-items:center;justify-content:space-between;margin-bottom:28px}
.plans-head h2{font-family:"Raleway",sans-serif;font-weight:500;font-size:42px}
.arrows{display:flex;gap:20px}
.arrow{width:50px;height:50px;border-radius:50%;background:#4a4a4a;display:flex;align-items:center;justify-content:center}
.poster{width:522px;height:256px;border:4px solid #eee;background:linear-gradient(135deg,#28b36a 0%,#e98a2a 45%,#a63a7a 70%,#2aa7c9 100%)}
.event-title{color:var(--orange);font-weight:700;font-size:28px;margin-top:34px}
.event-text{color:#cfcfcf;font-size:22px;line-height:36px;margin-top:4px}

.past{height:540px;padding:36px 40px 0 40px}
.section-title{font-family:"Raleway",sans-serif;font-weight:500;font-size:44px;color:var(--orange);margin-bottom:26px}
.past-grid{display:grid;grid-template-columns:1fr 270px;column-gap:24px;row-gap:26px}
.past-item h3{font-size:19px;font-weight:700;text-transform:uppercase;color:var(--black);line-height:24px}
.past-item .city{font-size:19px;line-height:26px}
.past-item .date{font-size:17px;color:var(--orange)}
.btn{display:inline-block;background:var(--orange);color:var(--white);font-weight:700;font-size:18px;padding:16px 26px;margin-top:8px}

.photos{height:510px;padding:0 40px}
.photo-grid{display:grid;grid-template-columns:repeat(3,1fr);gap:24px 20px}
.photo{height:160px;border:2px solid #ddd}
.p1{background:linear-gradient(135deg,#c86a2a,#6a4a3a)}
.p2{background:linear-gradient(135deg,#d88a3a,#8aa0b0)}
.p3{background:linear-gradient(135deg,#9a7a6a,#e07a2a)}
.p4{background:linear-gradient(135deg,#5a4030,#f08a30)}
.p5{background:linear-gradient(135deg,#2a2520,#7a5040)}
.p6{background:linear-gradient(135deg,#b0b8c0,#8a5a40)}

.footer{height:199px;background:var(--black);text-align:center;padding-top:54px}
.footer-links{display:flex;justify-content:center;gap:70px;color:var(--white);font-size:19px;text-transform:uppercase}
.copyright{color:#888;font-size:17px;margin-top:14px}
</style>
</head>
<body>
<div class="page">
  <header class="topbar">
    <div class="brand"><span class="brand-dot"></span>Partyvenz</div>
    <div class="topbar-icons">
      <svg width="40" height="48" viewBox="0 0 40 48" aria-label="Account"><circle cx="20" cy="13" r="11" fill="#fff"/><path d="M2 46c0-12 8-20 18-20s18 8 18 20z" fill="#fff"/></svg>
      <svg width="66" height="40" viewBox="0 0 66 40" aria-label="Menu"><rect y="2" width="66" height="5" fill="#fff"/><rect y="17" width="66" height="5" fill="#fff"/><rect y="32" width="66" height="5" fill="#fff"/></svg>
    </div>
  </header>

  <section class="hero">
    <div class="hero-photo" role="img" aria-label="Blurred party photo as profile cover"></div>
    <div class="hero-shade"></div>
    <div class="hero-inner">
      <div class="avatar" role="img" aria-label="Profile picture of the photographer"></div>
      <h1 class="profile-name">RIVOLENS PHOTOGRAPHY</h1>
      <div class="profile-meta">
        <div>Member since : January 1, 2006<span class="sep">/</span>Age : 34<span class="sep">/</span></div>
        <div>City : Amersfoort<span class="sep">/</span>Music : Latin<span class="sep">/</span>Salsa</div>
        <div>Active since: Jan 2006<span class="sep"></span>Shoots: 500 and counting</div>
      </div>
      <div class="socials"><span class="social" aria-label="Chatterbook"></span><span class="social" aria-label="Website"></span></div>
    </div>
  </section>

  <main class="bio">
    <div class="bio-block">
      <h2>Wil jij fotograferen voor Partyvenz?</h2>
      <p>Als je uitgaan leuk vindt, makkelijk bent in de omgang en uiteraard houdt van fotograferen, biedt Partyvenz je de kans een kijkje te nemen in de wereld van de partyfotografie. Door de inzet van de fotografen is Partyvenz uitgegroeid tot een van de meest toonaangevende partysites van Nederland. De betrouwbaarheid, de hoge kwaliteit van de foto's en het coveren van de belangrijkste evenementen maakt van Partyvenz een van de best bezochte websites in ons vakgebied</p>
    </div>
    <div class="bio-block">
      <h2>Belangrijk informatie</h2>
      <p>Fotograferen voor Partyvenz is op vrijwillige basis. Je kan kiezen waar en wanneer je uitgaat en foto's maakt, maar een vaste inbreng word wel van je verwacht. Hoe meer je voor Partyvenz doet, hoe meer ervaring je opdoet met de camera en hoe beter je word. Hierdoor kan je weer naar interessantere feesten en festivals. Wat je wel krijgt is gratis entree voor een evenement en soms ook andere voordelen zoals gratis drankjes.... je gaat meestal met ze tweetjes op pad en ontmoet veel nieuwe mensen zoals DJ's en organisatoren. Hoe meer je voor Partyvenz.example werkt hoe meer ervaring je er ook uit zal halen. De beste fotografen doen3</p>
    </div>
    <div class="bio-block">
      <h2>Voorwaarden</h2>
      <ul class="conditions">
        <li>Je moet 18 jaar of ouder zijn.</li>
        <li>Je moet het aankunnen om hoge kwaliteit foto's te maken en professioneel gedrag vertonen.</li>
        <li>Je moet sociaal zijn; een open persoon zijn die ervan houdt om ander e mensen te ontmoeten.</li>
        <li>Het is een vereiste dat je een digitale spiegelreflex-camera hebt en lichtsterke lens met vast diafragma van F2.8 en natuurlijk een externe flitser (E-TTL).</li>
        <li>Je bent verantwoordelijk voor je eigen vervoer om naar de evenementen te gaan waar je foto's maakt.</li>
      </ul>
    </div>
    <div class="bio-block">
      <h2>Aanmelden</h2>
      <p>Wil jij ook het team van Partyvenz versterken en het nachtleven van een andere kant verkennen? Geef je dan op, stuur een mailtje naar rivo@partyvenz.example Vermeld daar goed in je naam, leeftijd, woonplaats en het type camera dat je hebt en je ervaring op het gebied van fotograferen.</p>
      <p>Bekijk ons online foto album voor de door mij geschoten foto's. Bekijk al mijn Streamly filmpjes via mijn eigen Streamly kanaal</p>
    </div>
  </main>

  <section class="plans">
    <div class="plans-head">
      <h2>Event Plan to Go</h2>
      <div class="arrows">
        <span class="arrow"><svg width="14" height="20" viewBox="0 0 14 20"><path d="M11 2 3 10l8 8" stroke="#fff" stroke-width="3" fill="none"/></svg></span>
        <span class="arrow"><svg width="14" height="20" viewBox="0 0 14 20"><path d="m3 2 8 8-8 8" stroke="#fff" stroke-width="3" fill="none"/></svg></span>
      </div>
    </div>
    <div class="poster" role="img" aria-label="Colourful festival poster for the event on 9 July 2016"></div>
    <div class="event-title">Sis parturient mont</div>
    <p class="event-text">nascetur ridiculus mus In iaculis facilisis massa Etiam eu urna Sed porta Suspendis</p>
  </section>

  <section class="past">
    <h2 class="section-title">Past Events</h2>
    <div class="past-grid">
      <div class="past-item"><h3>Festival Sol Mundo 2016</h3><div class="city">Rotterdam</div><div class="date">25 March 2016</div></div>
      <div class="past-item"><h3>Donec convallis 2016</h3><div class="city">Rotterdam</div><div class="date">15 March 2016</div></div>
      <div class="past-item"><h3>Rhoncus dictum 2016</h3><div class="city">Rotterdam</div><div class="date">23 March 2016</div></div>
      <div class="past-item"><h3>Aliquam erat volutpa 2016</h3><div class="city">Rotterdam</div><div class="date">10 March 2016</div></div>
      <div class="past-item"><h3>Cras a ante vitae enim 2016</h3><div class="city">Rotterdam</div><div class="date">22 March 2016</div></div>
      <div class="past-item"><span class="btn">VIEW MORE</span></div>
    </div>
  </section>

  <section class="photos">
    <h2 class="section-title">Photos</h2>
    <div class="photo-grid">
      <div class="photo p1" role="img" aria-label="Party photo of visitors in orange"></div>
      <div class="photo p2" role="img" aria-label="Party photo of a crowd outdoors"></div>
      <div class="photo p3" role="img" aria-label="Party photo of two friends"></div>
      <div class="photo p4" role="img" aria-label="Party photo of festival goers"></div>
      <div class="photo p5" role="img" aria-label="Party photo taken at night"></div>
      <div class="photo p6" role="img" aria-label="Party photo of a street celebration"></div>
    </div>
  </section>

  <footer class="footer">
    <nav class="footer-links"><span>Contact</span><span>Terms of use</span><span>Privacy policy</span></nav>
    <div class="copyright">© 2016 Company Name  All right reserved</div>
  </footer>
</div>
</body>
</html>
```